Life Coaching business needs a new flyer

We are an Australian business that specialises in Life Coaching, Career Coaching, Health and Wellness Coaching, Yoga and Pilates. We need a A4 double sided flyer that is full colour and folded to DL format. I have attached a couple of designs that I like and some pictures and would like the flyer to be bright yet stylish.

Industry/Entity Type

Life Coaching

```html
<!DOCTYPE html>
<html lang="en">
<head>
<meta charset="utf-8">
<title>Bright Path Coaching Studio – DL Brochure</title>
<link href="https://fonts.googleapis.com/css2?family=Open+Sans:wght@400;600;700&family=Noto+Serif:wght@700&family=Parisienne&display=swap" rel="stylesheet">
<style>
:root{
  --bg:#c9c9c9;
  --paper:#ffffff;
  --ink:#2b2b2b;
  --muted:#555;
  --blue-deep:#3f6fb0;
  --blue-mid:#5f95d3;
  --blue-bright:#1f9ae0;
  --blue-head:#1a8fc9;
  --sky:#dcedf7;
  --green:#4fae1e;
  --green-dark:#3b9214;
  --tick:#5bb52a;
}
*{box-sizing:border-box;margin:0;padding:0}
html,body{width:1034px;height:1200px;overflow:hidden;background:var(--bg);font-family:"Open Sans",Arial,sans-serif;color:var(--ink)}
.canvas{width:1034px;height:1200px;padding:20px 22px;display:flex;flex-direction:column;gap:20px}
.sheet{width:990px;height:570px;display:flex;background:var(--paper);box-shadow:0 6px 18px rgba(0,0,0,.25)}
.panel{width:330px;height:100%;position:relative;overflow:hidden}
.photo{position:absolute;left:0;right:0;bottom:0}

/* outside */
.testimonials{background:linear-gradient(180deg,var(--blue-deep) 0%,var(--blue-mid) 55%,#a9cdf0 100%);color:#fff;padding:26px 24px}
.testimonials h2{font-family:"Noto Serif",Georgia,serif;font-size:17px;margin-bottom:10px}
.testimonials p{font-size:8.6px;line-height:1.42;margin-bottom:9px}
.testimonials .photo{height:180px;background:linear-gradient(180deg,rgba(169,205,240,0) 0%,#e58a5a 45%,#d94b5b 70%,#f1c9a4 100%)}

.intro{background:#eef2f5}
.intro-band{background:linear-gradient(180deg,var(--blue-bright),#3aa8ea);color:#fff;padding:28px 26px 30px;font-size:8.6px;line-height:1.45;border-bottom-left-radius:50% 30px;border-bottom-right-radius:50% 30px}
.intro-band p+p{margin-top:8px}
.offer{font-family:"Noto Serif",Georgia,serif;font-size:10px;text-align:center;line-height:1.35;padding:14px 20px 12px;color:#111}
.intro .photo{top:205px;bottom:auto;height:215px;background:linear-gradient(135deg,#8a7d6c 0%,#c9a98e 40%,#6d7c94 70%,#2e3b4d 100%)}
.contact{position:absolute;left:-10px;right:-10px;bottom:0;height:200px;background:radial-gradient(circle at 50% 40%,var(--green) 0%,var(--green-dark) 100%);border-top-left-radius:50% 70px;border-top-right-radius:50% 70px;color:#fff;text-align:center;padding-top:30px}
.contact h3{font-family:"Noto Serif",Georgia,serif;font-size:16px;margin-bottom:8px}
.contact .line{font-size:10.5px;margin-top:3px}
.contact svg{display:block;margin:6px auto 0}

.cover{background:linear-gradient(180deg,#e8f2f8 0%,var(--sky) 50%,#bfd9ea 100%);text-align:center;padding-top:28px}
.brand{display:flex;align-items:center;justify-content:center;gap:8px;font-family:"Open Sans",Arial,sans-serif;font-weight:700;font-size:15px;color:var(--green-dark);letter-spacing:.5px}
.brand-dot{width:14px;height:14px;border-radius:50%;background:var(--green)}
.cover-titles{font-family:"Parisienne",cursive;color:var(--blue-head);font-size:25px;line-height:1.25;margin-top:16px}
.cover .photo{height:320px;background:linear-gradient(180deg,#d3e6f1 0%,#b9d3e4 55%,#9fbfd6 100%)}

/* inside */
.inside .panel{padding:24px 22px}
.questions p.q{font-size:9.8px;font-weight:700;line-height:1.35;margin-bottom:7px}
.questions p.q.answer{margin-top:4px}
h4.section{font-family:"Noto Serif",Georgia,serif;color:var(--blue-head);font-size:15px;line-height:1.25;margin:12px 0 6px}
.body{font-size:9.4px;line-height:1.45;color:var(--muted);margin-bottom:7px}
.questions .photo{height:150px;background:linear-gradient(160deg,#2fc6c7 0%,#49d6cf 40%,#1aa4b3 75%,#e5507a 100%)}
.services .photo{height:110px;background:linear-gradient(180deg,#eaf4fb 0%,#9dcbe8 55%,#3b8ec9 100%)}
.help ul{list-style:none;margin:4px 0 6px}
.help li{font-size:9.2px;font-style:italic;color:var(--muted);display:flex;align-items:center;gap:5px;line-height:1.5}
.help li svg{flex:none}
.help .photo{height:150px;background:linear-gradient(120deg,#9bbf58 0%,#e8b36f 45%,#f2d2b0 70%,#c98b55 100%)}
</style>
</head>
<body>
<main class="canvas">

  <section class="sheet outside">
    <div class="panel testimonials">
      <h2>Happy Clients Testimonials</h2>
      <p>“I have lost 10 kilos and now have the energy to play with my kids. Thanks Jess for you support/guidance and helping me get rid of my limiting beliefs. I feel I can achieve anything now! The sky's the limit” Megan, Mosman</p>
      <p>“I had always wanted to start up own café however every time it came to putting it into practice I would procrastinate and not achieve anything. I became overwhelmed with the whole process and never achieved anything. Jess put it into bite sized chunks and helped me to set small achievable goals. I am now a happy café owner.” Tara, Double Bay</p>
      <p>“Jess has helped to change my life around in all aspects. I would have been lost without her. Thanks Jess for your professionalism, support and guidance.” Chloe, Cremorne</p>
      <p>“I was so busy with kids, work, and my husband I lost who I was. Jess has helped me find the person I am again.” Emma, Chatswood</p>
      <p>“When I started with Coach Jess, I didn't know anything about coaching. I called her because she helped a friend of mine make a career change that was a perfect fit for her. I had the opportunity to make a change too and did not know where to start. I am now in a job that I love. I would recommend Jess to everyone.” Daniel, Texas America</p>
      <div class="photo" role="img" aria-label="Photo of four happy friends jumping with arms raised against a blue sky"></div>
    </div>

    <div class="panel intro">
      <div class="intro-band">
        <p>Bright Path Coaching Studio is a professional service that can help you achieve the goals that you are looking for in Life Coaching, Meditation, and Yoga/Pilates.</p>
        <p>If you are ready to take your life to the next level and would like to know more, please</p>
      </div>
      <p class="offer">Free Introductory Life Coaching<br>Phone/Video Call session – 20 mins<br>(To see if coaching is right for you)</p>
      <div class="photo" role="img" aria-label="Portrait photo of the two coaches, a woman and a man, smiling"></div>
      <div class="contact">
        <h3>contact us.</h3>
        <svg width="14" height="14" viewBox="0 0 24 24" aria-hidden="true"><path fill="#fff" d="M6.6 10.8a15 15 0 0 0 6.6 6.6l2.2-2.2a1 1 0 0 1 1-.25 11.4 11.4 0 0 0 3.6.57 1 1 0 0 1 1 1V20a1 1 0 0 1-1 1A17 17 0 0 1 3 4a1 1 0 0 1 1-1h3.5a1 1 0 0 1 1 1c0 1.25.2 2.45.57 3.57a1 1 0 0 1-.25 1z"/></svg>
        <div class="line">02 9000 4417</div>
        <svg width="14" height="11" viewBox="0 0 24 18" aria-hidden="true"><rect x="1" y="1" width="22" height="16" rx="1" fill="none" stroke="#fff" stroke-width="2"/><path d="M1 2l11 8 11-8" fill="none" stroke="#fff" stroke-width="2"/></svg>
        <div class="line">hello@brightpathcoaching.com.au</div>
        <svg width="14" height="14" viewBox="0 0 24 24" aria-hidden="true"><circle cx="12" cy="12" r="10" fill="none" stroke="#fff" stroke-width="2"/><path d="M2 12h20M12 2c3 3 3 17 0 20M12 2c-3 3-3 17 0 20" fill="none" stroke="#fff" stroke-width="1.6"/></svg>
        <div class="line">brightpathcoaching.com.au</div>
      </div>
    </div>

    <div class="panel cover">
      <div class="brand"><span class="brand-dot"></span>Bright Path Coaching Studio</div>
      <div class="cover-titles">Life Coaching<br>Meditation<br>Yoga/Pilates</div>
      <div class="photo" role="img" aria-label="Photo of a man and woman doing a yoga tree pose on a beach by the sea"></div>
    </div>
  </section>

  <section class="sheet inside">
    <div class="panel questions">
      <p class="q">Are you looking at making changes this year?</p>
      <p class="q">Are you stuck in a rut or at a crossroad in your life?</p>
      <p class="q">Are you wanting to lose weigh but can't get motivated?</p>
      <p class="q">Do you have ongoing problems with your career, relationships, or just life itself?</p>
      <p class="q answer">Life coaching is the answer</p>
      <h4 class="section">Bright Path Coaching Studio</h4>
      <p class="body">Our mission is to help you become the best possible person you can be. Mentally, physically, and spiritually.</p>
      <p class="body">We offer highly qualified and compassionate trainers/coaches for Life Coaching, Meditation, Yoga and Pilates.</p>
      <p class="body">They will guide and motivate you every step of the way to achieve all your dreams and goals.</p>
      <p class="body">They will make you be the best you can be</p>
      <div class="photo" role="img" aria-label="Photo of a woman floating on a pink lilo in clear turquoise water"></div>
    </div>

    <div class="panel services">
      <h4 class="section" style="margin-top:0">Life Coaching</h4>
      <p class="body">Your Life Coach will give you the confidence and the ability to move forward in a positive manner in all areas of your life where you crave change.</p>
      <p class="body">Life Coaching is about breaking down the barriers preventing this change from happening, and creating the ideal environment for positive action to take place. It is a holistic approach, which looks at the present and sets goals for a totally successful future.</p>
      <h4 class="section">Career Coaching</h4>
      <p class="body">Are you at a crossroads in your career and at a loss about what to do next? Do you want your work to be in alignment with the authentic you? It can be difficult to assess career options, goals, and strategies, and have the confidence to implement changes on your own. With the right coaching support, you will gain the clarity that you need to take control and have a fulfilling and rewarding career.</p>
      <h4 class="section">Wellness Coaching</h4>
      <p class="body">Health and wellness coaches help their clients find the motivation and tools to achieve their health and wellness goals, working with the client to examine and improve the psychological framework that supports those goals.</p>
      <div class="photo" role="img" aria-label="Photo of a woman in white holding a balancing yoga pose by the sea"></div>
    </div>

    <div class="panel help">
      <h4 class="section" style="margin-top:0">Why Would I Need Help?</h4>
      <p class="body">Coaching is for anyone who wants to make lasting changes in their life. Coaching can assist with such issues as:</p>
      <ul>
        <li><svg width="9" height="9" viewBox="0 0 10 10" aria-hidden="true"><circle cx="5" cy="5" r="5" fill="var(--tick)"/><path d="M2.5 5.2l1.7 1.6 3.3-3.4" fill="none" stroke="#fff" stroke-width="1.3"/></svg>Creating a better work- life balance</li>
        <li><svg width="9" height="9" viewBox="0 0 10 10" aria-hidden="true"><circle cx="5" cy="5" r="5" fill="var(--tick)"/><path d="M2.5 5.2l1.7 1.6 3.3-3.4" fill="none" stroke="#fff" stroke-width="1.3"/></svg>Resolving relationship issues</li>
        <li><svg width="9" height="9" viewBox="0 0 10 10" aria-hidden="true"><circle cx="5" cy="5" r="5" fill="var(--tick)"/><path d="M2.5 5.2l1.7 1.6 3.3-3.4" fill="none" stroke="#fff" stroke-width="1.3"/></svg>Career guidance</li>
        <li><svg width="9" height="9" viewBox="0 0 10 10" aria-hidden="true"><circle cx="5" cy="5" r="5" fill="var(--tick)"/><path d="M2.5 5.2l1.7 1.6 3.3-3.4" fill="none" stroke="#fff" stroke-width="1.3"/></svg>Stress management</li>
        <li><svg width="9" height="9" viewBox="0 0 10 10" aria-hidden="true"><circle cx="5" cy="5" r="5" fill="var(--tick)"/><path d="M2.5 5.2l1.7 1.6 3.3-3.4" fill="none" stroke="#fff" stroke-width="1.3"/></svg>Weight loss and fitness</li>
        <li><svg width="9" height="9" viewBox="0 0 10 10" aria-hidden="true"><circle cx="5" cy="5" r="5" fill="var(--tick)"/><path d="M2.5 5.2l1.7 1.6 3.3-3.4" fill="none" stroke="#fff" stroke-width="1.3"/></svg>Motivation and goal setting</li>
        <li><svg width="9" height="9" viewBox="0 0 10 10" aria-hidden="true"><circle cx="5" cy="5" r="5" fill="var(--tick)"/><path d="M2.5 5.2l1.7 1.6 3.3-3.4" fill="none" stroke="#fff" stroke-width="1.3"/></svg>Boosting your self esteem</li>
        <li><svg width="9" height="9" viewBox="0 0 10 10" aria-hidden="true"><circle cx="5" cy="5" r="5" fill="var(--tick)"/><path d="M2.5 5.2l1.7 1.6 3.3-3.4" fill="none" stroke="#fff" stroke-width="1.3"/></svg>Overcoming negative emotions and thoughts</li>
        <li><svg width="9" height="9" viewBox="0 0 10 10" aria-hidden="true"><circle cx="5" cy="5" r="5" fill="var(--tick)"/><path d="M2.5 5.2l1.7 1.6 3.3-3.4" fill="none" stroke="#fff" stroke-width="1.3"/></svg>Better time management</li>
      </ul>
      <h4 class="section">Meditation</h4>
      <p class="body">We specialise in teaching meditation from beginners to advanced and teach a variety of techniques for stress reduction, peace of mind, stillness, and clarity.</p>
      <h4 class="section">Yoga/Pilates</h4>
      <p class="body">Your highly qualified and experienced Yoga or Pilates instructor will come to you and create a fun and varied workout based on what you enjoy and what your goals are.</p>
      <div class="photo" role="img" aria-label="Photo of a mother and young daughter hugging outdoors in warm sunlight"></div>
    </div>
  </section>

</main>
</body>
</html>
```